Retail/Wholesale website graphic template

I need to design a new graphic template for a website for a client. The website will be a retail/wholesale company site with most pages dedicated to presentation. There will also be an online store and a blog. However, you don't need to worry about those. All I need from you is a graphic template for a generic site page.

It will need to include standard UI elements, in case I need those. I am attaching a more detailed assignment in .docx format.

The logo is also attached.

Target Market(s)

small business owners, (occasional) retail customers

Industry/Entity Type

Wholesale

Number of Pages Required

1 page

Font styles to use
Serif
Sans Serif

Colors
ec1f27
474747

Requirements
Must have
• must match logo, be clean, minimal and with slightly larger text size
Should not have
• must not be modern-looking where you have to scroll and scroll and scroll to get to the bottom of the homepage. most of my visitors are "old" people, they do not get this type of design.

```html
<!DOCTYPE html>
<html lang="en">
<head>
<meta charset="utf-8">
<title>Beacon Imports</title>
<link href="https://fonts.googleapis.com/css2?family=Lato:wght@400;700;900&display=swap" rel="stylesheet">
<style>
:root{
  --red:#ec1f27;
  --dark:#333333;
  --grey:#474747;
  --text:#4a4a4a;
  --light:#f4f4f4;
  --white:#ffffff;
}
*{box-sizing:border-box;margin:0;padding:0}
html,body{width:1200px;height:3600px;overflow:hidden}
body{font-family:"Lato",Arial,sans-serif;color:var(--text);background:var(--white);position:relative}
.abs{position:absolute}
.topbar{left:0;top:0;width:1200px;height:48px;background:var(--dark);color:#fff;font-size:15px;display:flex;justify-content:flex-end;align-items:center;gap:56px;padding-right:74px}
.topbar span{display:flex;align-items:center;gap:10px}
.nav{left:0;top:48px;width:1200px;height:91px;background:#fff;display:flex;align-items:center;justify-content:space-between;padding:0 74px}
.brand{display:flex;align-items:center;gap:10px;color:var(--red);font-weight:700;font-size:26px;line-height:1;white-space:nowrap}
.brand-mark{width:18px;height:18px;background:var(--red);display:block}
.menu{display:flex;gap:44px;font-size:14px;font-weight:700;color:var(--grey)}
.menu .active{color:var(--red)}
.hero{left:0;top:139px;width:1200px;height:523px;background:linear-gradient(135deg,#6d6a5c,#a8987a 40%,#5b6b8a 70%,#3d4a63)}
.hero-inner{position:absolute;left:0;top:165px;width:1200px;text-align:center;color:#fff}
.hero h1{font-size:74px;font-weight:900;line-height:1;text-shadow:0 2px 8px rgba(0,0,0,.4)}
.hero p{font-size:38px;font-weight:700;margin-top:10px;text-shadow:0 2px 8px rgba(0,0,0,.4)}
.btn{display:inline-block;width:180px;height:40px;line-height:40px;border-radius:20px;background:var(--red);color:#fff;font-size:14px;font-weight:700;text-align:center}
.hero .btn{margin-top:14px}
.dots{position:absolute;top:488px;left:0;width:1200px;display:flex;justify-content:center;gap:8px}
.dots i{width:9px;height:9px;border-radius:50%;background:#fff;display:block}
.section-title{font-size:34px;font-weight:700;color:var(--dark);text-align:center;letter-spacing:1px}
.rule{width:72px;height:3px;background:var(--red);margin:18px auto 0}
.overview{left:0;top:662px;width:1200px;height:418px;text-align:center;padding-top:78px}
.overview p{font-size:16.5px;line-height:28px;width:1040px;margin:24px auto 0}
.overview .btn{margin-top:30px}
.services{left:0;top:1080px;width:1200px;height:713px;background:linear-gradient(var(--dark) 0 343px,#fff 343px)}
.services .section-title{color:#fff;padding-top:52px}
.services .lead{color:#fff;text-align:center;font-size:16.5px;margin-top:26px}
.svc{position:absolute;top:185px;width:512px}
.svc .photo{height:233px}
.svc h3{color:var(--red);font-size:19px;font-weight:700;margin-top:32px}
.svc p{font-size:15px;line-height:28px;margin-top:8px}
.svc .btn{margin-top:26px}
.gallery{left:0;top:1793px;width:1200px;height:516px;background:var(--light);padding-top:52px}
.tile{position:absolute}
.process{left:0;top:2309px;width:1200px;height:480px;background:#fff}
.process h2{position:absolute;left:588px;top:82px;font-size:34px;font-weight:700;color:var(--dark)}
.process .rule{position:absolute;left:588px;top:136px;margin:0}
.process p{position:absolute;left:588px;top:168px;width:540px;font-size:16.5px;line-height:30.5px}
.process .btn{position:absolute;left:588px;top:352px}
.blog{left:0;top:2789px;width:1200px;height:350px;background:var(--light);padding-top:46px}
.post{position:absolute;top:146px;width:340px}
.post h3{color:var(--red);font-size:19px;font-weight:700}
.post p{font-size:14.5px;line-height:24px;margin-top:12px}
.post a{display:block;margin-top:10px;font-size:12.5px;font-weight:900;color:var(--dark);text-decoration:none}
.footer{left:0;top:3139px;width:1200px;height:461px;background:var(--dark);color:#fff}
.footer .brand{position:absolute;left:74px;top:62px;color:#fff;font-size:24px}
.footer .brand-mark{background:#fff;width:16px;height:16px}
.fcol{position:absolute;top:138px}
.fcol h4{font-size:18px;font-weight:700;margin-bottom:14px}
.fcol li{list-style:none;font-size:14px;line-height:31px;color:#e6e6e6}
.fcol .row{display:flex;align-items:center;gap:18px}
.fbottom{position:absolute;left:74px;top:389px;width:1052px;border-top:1px solid #555;height:72px;display:flex;justify-content:space-between;align-items:center;font-size:12px;color:#ccc}
.social{display:flex;gap:22px}
.social i{width:20px;height:20px;border-radius:50%;background:#ddd;display:block}
</style>
</head>
<body>

<header class="abs topbar">
  <span><svg width="14" height="14" viewBox="0 0 24 24"><path fill="#fff" d="M6.6 10.8a15 15 0 006.6 6.6l2.2-2.2a1 1 0 011-.25 11.4 11.4 0 003.6.6 1 1 0 011 1V20a1 1 0 01-1 1A17 17 0 013 4a1 1 0 011-1h3.5a1 1 0 011 1c0 1.25.2 2.45.6 3.6a1 1 0 01-.25 1z"/></svg>1-800-555-0142</span>
  <span><svg width="15" height="12" viewBox="0 0 24 18"><rect width="24" height="18" rx="2" fill="#fff"/><path d="M1 2l11 8 11-8" stroke="#333" stroke-width="2" fill="none"/></svg>hello@beaconimports.example</span>
  <span><svg width="13" height="14" viewBox="0 0 24 24"><circle cx="12" cy="7" r="5" fill="#fff"/><path d="M2 24a10 10 0 0120 0z" fill="#fff"/></svg>Log In</span>
</header>

<nav class="abs nav">
  <div class="brand"><i class="brand-mark"></i>Beacon Imports</div>
  <div class="menu">
    <span class="active">HOME</span><span>ABOUT US</span><span>SERVICES</span><span>PRODUCT GALLERY</span><span>OUR PROCESS</span><span>BLOG</span><span>CONTACT US</span>
  </div>
</nav>

<section class="abs hero" role="img" aria-label="Warehouse aisles stacked with boxed goods on pallets">
  <div class="hero-inner">
    <h1>BEACON IMPORTS</h1>
    <p>We are a retail &amp; whole sale import company.</p>
    <span class="btn">READ MORE</span>
  </div>
  <div class="dots"><i></i><i></i><i></i></div>
</section>

<section class="abs overview">
  <h2 class="section-title">COMPANY OVERVIEW</h2>
  <div class="rule"></div>
  <p>Lorem ipsum dolor sit amet, consectetur adipisicing elit, sed do eiusmod tempor incididunt ut labore et doloreasdes magna aliqua.<br>Ut enim ad minim veniam, quis nostrud exercitation ullamco laboris nisi ut aliquip ex ea commodalo consequat. Duis aute irure dolor in<br>reprehenderit in voluptate velit esse cillum dolore eu fugiat nulla pariatur. Excepteur sint occaecat cupidatat non proident,<br>sunt in culpa qui officia deserunt mollit anim id est laborum.</p>
  <span class="btn">READ MORE</span>
</section>

<section class="abs services">
  <h2 class="section-title">OUR SERVICES</h2>
  <p class="lead">Lorem ipsum dolor sit amet, consectetur adipisicing elit, sed do eiusmod tempor incididunt ut labore et doloreasdes magna aliqua.</p>
  <article class="svc" style="left:74px">
    <div class="photo" role="img" aria-label="Retail store shelves with colourful packaged goods" style="background:linear-gradient(135deg,#c9c2c6,#b8485a 45%,#7a8fb0)"></div>
    <h3>RETAIL SALE IMPORT</h3>
    <p>Lorem ipsum dolor sit amet, consectetur adipisicing elit, sed do eiusmod tempor incididunt ut labore et doloreasdes magna aliqua ad minim veniam, quis nostrud exercitation ullamco laboris nisi ut aliquip ex ea commodalo consequat dolor in reprehenderit..</p>
    <span class="btn">READ MORE</span>
  </article>
  <article class="svc" style="left:617px">
    <div class="photo" role="img" aria-label="Wholesale warehouse aisle with tall stocked racks" style="background:linear-gradient(135deg,#5a5f7a,#a67a5a 45%,#3f4966)"></div>
    <h3>WHOLE SALE IMPORT</h3>
    <p>Lorem ipsum dolor sit amet, consectetur adipisicing elit, sed do eiusmod tempor incididunt ut labore et doloreasdes magna aliqua ad minim veniam, quis nostrud exercitation ullamco laboris nisi ut aliquip ex ea commodalo consequat dolor in reprehenderit..</p>
    <span class="btn">READ MORE</span>
  </article>
</section>

<section class="abs gallery">
  <h2 class="section-title">PRODUCT GALLERY</h2>
  <div class="rule"></div>
  <div class="tile" role="img" aria-label="Fresh fish on ice with lemon slices" style="left:74px;top:149px;width:332px;height:304px;background:linear-gradient(135deg,#9aa6ae,#d7d6cc 50%,#6f7f8a);border:5px solid var(--red)"></div>
  <div class="tile" role="img" aria-label="Pile of colourful fresh fruit" style="left:420px;top:149px;width:211px;height:146px;background:linear-gradient(135deg,#d8331f,#e9a320 50%,#6c9a2a)"></div>
  <div class="tile" role="img" aria-label="Racks of colourful clothing" style="left:643px;top:149px;width:211px;height:146px;background:linear-gradient(135deg,#3a3a4a,#c05a8a 50%,#4a7aa0)"></div>
  <div class="tile" role="img" aria-label="Hanging decorative lamps" style="left:420px;top:307px;width:211px;height:146px;background:linear-gradient(135deg,#3e3a36,#b07050 50%,#7a5a40)"></div>
  <div class="tile" role="img" aria-label="Paper grocery bag filled with vegetables" style="left:643px;top:307px;width:211px;height:146px;background:linear-gradient(135deg,#8a8280,#c7a070 50%,#6a8a4a)"></div>
  <div class="tile" role="img" aria-label="Shopper choosing a product from a supermarket shelf" style="left:869px;top:149px;width:257px;height:304px;background:linear-gradient(135deg,#d8d4cc,#c9a48a 50%,#9ab0c8)"></div>
</section>

<section class="abs process">
  <div role="img" aria-label="Isometric illustration of warehouses, trucks and a delivery route" style="position:absolute;left:120px;top:74px;width:396px;height:334px;background:linear-gradient(135deg,#cfd6dc,#3f8aa6 55%,#2f6a82);border-radius:8px"></div>
  <h2>OUR PROCESS</h2>
  <div class="rule"></div>
  <p>Lorem ipsum dolor sit amet, consectetur adipisicing elit, sed do eiusmod tempor incididunt ut labore et doloreasdes magna aliqua. Ut enim ad minim veniam, quis nostrud exercitation ullamco laboris nisi ut aliquip ex ea commodalo consequat. Duis aute irure dolor in reprehenderit in voluptate velit esse cillum dolore eu fugiat nulla pariatur.</p>
  <span class="btn">READ MORE</span>
</section>

<section class="abs blog">
  <h2 class="section-title">BLOG POST</h2>
  <div class="rule"></div>
  <article class="post" style="left:74px"><h3>VOLUPTATE VELIT ESSE CILLUM</h3><p>Lorem ipsum dolor sit amet, consectetur adipisicing elit, sed do eiusmod tempor ut labore et doloreasdes incididunt...</p><a>READ MORE &gt;&gt;</a></article>
  <article class="post" style="left:434px"><h3>VOLUPTATE VELIT ESSE CILLUM</h3><p>Lorem ipsum dolor sit amet, consectetur adipisicing elit, sed do eiusmod tempor ut labore et doloreasdes incididunt...</p><a>READ MORE &gt;&gt;</a></article>
  <article class="post" style="left:790px"><h3>VOLUPTATE VELIT ESSE CILLUM</h3><p>Lorem ipsum dolor sit amet, consectetur adipisicing elit, sed do eiusmod tempor ut labore et doloreasdes incididunt...</p><a>READ MORE &gt;&gt;</a></article>
</section>

<footer class="abs footer">
  <div class="brand"><i class="brand-mark"></i>Beacon Imports</div>
  <div class="fcol" style="left:74px"><h4>Our Products</h4><ul><li>Lorem ipsum</li><li>Dolor sit amet consectetur</li><li>Adipisicing elit</li><li>Sed do eiusmod</li><li>Beatae vitae dicta</li><li>Sunt explicabo</li></ul></div>
  <div class="fcol" style="left:343px"><h4>Our Process</h4><ul><li>Lorem ipsum</li><li>Dolor sit amet consectetur</li><li>Adipisicing elit</li><li>Sed do eiusmod</li><li>Beatae vitae dicta</li><li>Sunt explicabo</li></ul></div>
  <div class="fcol" style="left:617px"><h4>About Us</h4><ul><li>Lorem ipsum</li><li>Dolor sit amet consectetur</li><li>Adipisicing elit</li><li>Sed do eiusmod</li></ul></div>
  <div class="fcol" style="left:885px"><h4>Contact Us</h4><ul>
    <li style="line-height:22px">14 Harbor Lane, Suite 2,<br>Portsmouth City, USA</li>
    <li class="row" style="margin-top:6px"><svg width="13" height="13" viewBox="0 0 24 24"><path fill="#fff" d="M6.6 10.8a15 15 0 006.6 6.6l2.2-2.2a1 1 0 011-.25 11.4 11.4 0 003.6.6 1 1 0 011 1V20a1 1 0 01-1 1A17 17 0 013 4a1 1 0 011-1h3.5a1 1 0 011 1c0 1.25.2 2.45.6 3.6a1 1 0 01-.25 1z"/></svg>1-800-555-0142</li>
    <li class="row"><svg width="14" height="11" viewBox="0 0 24 18"><rect width="24" height="18" rx="2" fill="#fff"/><path d="M1 2l11 8 11-8" stroke="#333" stroke-width="2" fill="none"/></svg>hello@beaconimports.example</li>
  </ul></div>
  <div class="fbottom">
    <span>Copyright © 2018 Beacon Imports. All Rights Reserved. Privacy Policy</span>
    <div class="social"><i></i><i></i><i></i><i></i><i></i></div>
  </div>
</footer>

</body>
</html>
```